Biz cards, stationary, envelopes for Bright Hollow Church
Bright Hollow Church marketing package
Designers,
Thank all of you for your creativity and your contributions to this project. As our first project we are well pleased with the outcome and look forward to seeing you on future projects we post in the future.
Best wishes...
RW
Designers,just wanted to say all of you have submitted amazing drafts! For finalization, would like the "P" in logo to be the same brown color as "church." Some of you have already done so but this brings some consistency to the cards. Again nice designs! RW
KT/FRN/DV Team
Designers, can we have an option 2 for the back of the card under logo to read: 2 Cor. 5:18-20 (bold). Also please write "Church" in sentence case. Nice designs!!

```html
<!DOCTYPE html>
<html lang="en">
<head>
<meta charset="utf-8">
<title>Bright Hollow Church – Stationery Set</title>
<link href="https://fonts.googleapis.com/css2?family=Open+Sans:wght@400;600;700&display=swap" rel="stylesheet">
<style>
:root{
  --backdrop:#e4d6bf;
  --paper:#ffffff;
  --navy:#1a2f7a;
  --blue:#2445a8;
  --sky:#5f8fd8;
  --gold:#d7a81c;
  --gold-light:#f2d764;
  --ink:#333a4a;
  --line:#9aa3b5;
  --faint:#eef1f6;
}
*{box-sizing:border-box;margin:0;padding:0}
html,body{width:1200px;height:674px;overflow:hidden}
body{background:var(--backdrop);font-family:"Open Sans",Arial,sans-serif;color:var(--ink);position:relative}
.item{position:absolute}
.label{position:absolute;font-size:8px;font-weight:600;color:#2a2a2a;white-space:nowrap;text-align:center}
.sheet{background:var(--paper);box-shadow:0 2px 6px rgba(0,0,0,.25);overflow:hidden}
.brand{display:flex;align-items:center;gap:5px}
.brand-dot{border-radius:50%;background:var(--blue);flex:none}
.brand-name{font-weight:700;color:var(--navy);line-height:1.1}
.wave{position:absolute;left:0;bottom:0;width:100%}
.watermark{position:absolute;border-radius:50%;border:18px solid var(--faint);left:50%;top:50%;transform:translate(-50%,-50%)}
.footer-text{position:absolute;right:14px;bottom:6px;font-size:5px;color:#fff;line-height:1.5;text-align:right}
/* business cards */
.card{width:127px;height:82px}
.card-front{width:214px;height:84px}
.card-center{display:flex;align-items:center;justify-content:center;height:100%}
.card-blue{background:radial-gradient(circle at 50% 45%,var(--sky),var(--blue) 60%,var(--navy))}
.card-gold{background:radial-gradient(circle at 50% 45%,var(--gold-light),var(--gold) 65%,#9c7410)}
.card-contact{position:absolute;right:8px;top:20px;font-size:5px;line-height:1.5;text-align:right;color:var(--ink)}
/* fax */
.fax-title{position:absolute;right:22px;top:66px;font-size:8px;font-weight:700;color:var(--ink)}
.fax-table{position:absolute;left:22px;top:78px;width:306px;border-collapse:collapse;font-size:6px}
.fax-table td{border:1px solid var(--line);height:14px;padding:0 4px}
.fax-table .key{width:38px;font-weight:600}
.fax-checks{position:absolute;left:22px;top:146px;display:flex;gap:14px;font-size:5.5px}
.fax-checks span::before{content:"";display:inline-block;width:6px;height:6px;border:1px solid var(--line);margin-right:3px;vertical-align:-1px}
/* envelopes */
.envelope{width:408px;height:252px}
.env-return{position:absolute;left:16px;top:16px}
.env-address{font-size:5.5px;line-height:1.5;margin-top:3px;color:var(--ink)}
.env-back{width:408px;height:118px}
.flap{position:absolute;left:0;top:0;width:100%;height:100%}
.flap-logo{position:absolute;left:50%;top:44px;transform:translateX(-50%);width:20px;height:20px;border-radius:50%;background:var(--blue);border:2px solid #fff}
.env-caption{position:absolute;width:100%;text-align:center;top:26px;font-size:7px;font-weight:600;color:#fff}
</style>
</head>
<body>

<!-- Business cards -->
<div class="label" style="left:43px;top:35px;width:214px">Business Card (Front)</div>
<div class="item sheet card-front" style="left:43px;top:48px">
  <div class="brand" style="position:absolute;left:10px;top:10px">
    <span class="brand-dot" style="width:14px;height:14px"></span>
    <span class="brand-name" style="font-size:10px">Bright Hollow<br>Church</span>
  </div>
  <div class="card-contact"><b>Senior Pastor</b><br>(555) 014-2290<br>info@brighthollow.org<br>www.brighthollow.org</div>
  <svg class="wave" viewBox="0 0 214 22" height="22" preserveAspectRatio="none">
    <path d="M0 7 C60 22 140 2 214 14 L214 22 L0 22Z" fill="var(--blue)"/>
    <path d="M0 3 C60 18 140 -2 214 10" stroke="var(--gold)" stroke-width="1.5" fill="none"/>
  </svg>
</div>

<div class="label" style="left:269px;top:37px;width:127px">Business Card (Back) Option 1</div>
<div class="item sheet card" style="left:269px;top:50px">
  <div class="card-center"><div class="brand"><span class="brand-dot" style="width:12px;height:12px"></span><span class="brand-name" style="font-size:8px">Bright Hollow<br>Church</span></div></div>
</div>

<div class="label" style="left:408px;top:37px;width:127px">Business Card (Back) Option 2</div>
<div class="item sheet card card-blue" style="left:408px;top:50px">
  <div class="card-center"><div class="brand"><span class="brand-dot" style="width:12px;height:12px;background:#fff"></span><span class="brand-name" style="font-size:8px;color:#fff">Bright Hollow<br>Church</span></div></div>
</div>

<div class="label" style="left:547px;top:37px;width:127px">Business Card (Back) Option 3</div>
<div class="item sheet card card-gold" style="left:547px;top:50px">
  <div class="card-center"><div class="brand"><span class="brand-dot" style="width:12px;height:12px"></span><span class="brand-name" style="font-size:8px">Bright Hollow<br>Church</span></div></div>
</div>

<!-- Fax cover -->
<div class="label" style="left:31px;top:150px;width:348px">Fax Cover</div>
<div class="item sheet" style="left:31px;top:163px;width:348px;height:490px">
  <div class="watermark" style="width:190px;height:190px"></div>
  <div class="brand" style="position:absolute;left:22px;top:22px">
    <span class="brand-dot" style="width:20px;height:20px"></span>
    <span class="brand-name" style="font-size:12px">Bright Hollow<br>Church</span>
  </div>
  <div class="fax-title">FAX</div>
  <table class="fax-table">
    <tr><td class="key">To:</td><td></td><td class="key">From:</td><td></td></tr>
    <tr><td class="key">Fax:</td><td></td><td class="key">Date:</td><td></td></tr>
    <tr><td class="key">Phone:</td><td></td><td class="key">Pages:</td><td></td></tr>
    <tr><td class="key">Re:</td><td></td><td class="key">Cc:</td><td></td></tr>
  </table>
  <div class="fax-checks"><span>Urgent</span><span>For Review</span><span>Please Comment</span><span>Please Reply</span><span>Please Recycle</span></div>
  <svg class="wave" viewBox="0 0 348 60" height="60" preserveAspectRatio="none">
    <path d="M0 18 C110 52 230 4 348 24 L348 60 L0 60Z" fill="var(--blue)"/>
    <path d="M0 12 C110 46 230 -4 348 16" stroke="var(--gold)" stroke-width="3" fill="none"/>
  </svg>
  <div class="footer-text">418 Hollow Ridge Rd, Fairview<br>Tel (555) 014-2290<br>info@brighthollow.org<br>www.brighthollow.org</div>
</div>

<!-- Letterhead -->
<div class="label" style="left:396px;top:150px;width:336px">Letterhead</div>
<div class="item sheet" style="left:396px;top:163px;width:336px;height:490px">
  <div class="watermark" style="width:190px;height:190px"></div>
  <div class="brand" style="position:absolute;left:22px;top:22px">
    <span class="brand-dot" style="width:20px;height:20px"></span>
    <span class="brand-name" style="font-size:12px">Bright Hollow<br>Church</span>
  </div>
  <svg class="wave" viewBox="0 0 336 60" height="60" preserveAspectRatio="none">
    <path d="M0 18 C110 52 220 4 336 24 L336 60 L0 60Z" fill="var(--blue)"/>
    <path d="M0 12 C110 46 220 -4 336 16" stroke="var(--gold)" stroke-width="3" fill="none"/>
  </svg>
  <div class="footer-text">418 Hollow Ridge Rd, Fairview<br>Tel (555) 014-2290<br>info@brighthollow.org<br>www.brighthollow.org</div>
</div>

<!-- Envelope front -->
<div class="label" style="left:763px;top:35px;width:408px">Envelopes (Front)</div>
<div class="item sheet envelope" style="left:763px;top:48px">
  <div class="env-return">
    <div class="brand"><span class="brand-dot" style="width:14px;height:14px"></span><span class="brand-name" style="font-size:9px">Bright Hollow<br>Church</span></div>
    <div class="env-address">418 Hollow Ridge Rd<br>Fairview, ST 00000</div>
  </div>
  <svg class="wave" viewBox="0 0 408 40" height="40" preserveAspectRatio="none">
    <path d="M0 14 C130 38 270 2 408 16 L408 40 L0 40Z" fill="var(--blue)"/>
    <path d="M0 9 C130 33 270 -3 408 11" stroke="var(--gold)" stroke-width="2.5" fill="none"/>
  </svg>
</div>

<!-- Envelope backs -->
<div class="label" style="left:763px;top:319px;width:408px">Envelopes (Back) Option 1</div>
<div class="item sheet env-back" style="left:763px;top:332px">
  <svg class="flap" viewBox="0 0 408 118" preserveAspectRatio="none">
    <path d="M0 0 L408 0 L408 10 L214 60 Q204 64 194 60 L0 10Z" fill="#f3f5f9" stroke="#cfd5e0"/>
  </svg>
  <div class="flap-logo"></div>
</div>

<div class="item sheet env-back" style="left:763px;top:430px">
  <svg class="flap" viewBox="0 0 408 118" preserveAspectRatio="none">
    <defs><linearGradient id="flapBlue" x1="0" y1="0" x2="0" y2="1"><stop offset="0" stop-color="var(--navy)"/><stop offset="1" stop-color="var(--sky)"/></linearGradient></defs>
    <path d="M0 0 L408 0 L408 10 L214 60 Q204 64 194 60 L0 10Z" fill="url(#flapBlue)"/>
  </svg>
  <div class="env-caption">Envelopes (Back) Option 2</div>
  <div class="flap-logo"></div>
</div>

<div class="item sheet env-back" style="left:763px;top:528px">
  <svg class="flap" viewBox="0 0 408 118" preserveAspectRatio="none">
    <defs><linearGradient id="flapGold" x1="0" y1="0" x2="0" y2="1"><stop offset="0" stop-color="#a57a10"/><stop offset="1" stop-color="var(--gold-light)"/></linearGradient></defs>
    <path d="M0 0 L408 0 L408 10 L214 60 Q204 64 194 60 L0 10Z" fill="url(#flapGold)"/>
  </svg>
  <div class="env-caption">Envelopes (Back) Option 3</div>
  <div class="flap-logo"></div>
</div>

</body>
</html>
```